Sparrow Haulage needs a business card design.

Design a double-sided business card for new freight business. On the front, would like to see our logo along with the following info:

Martin Obuya
CEO/FOUNDER
555-206-7142
martinobuya@sparrow-haulage.example

On the reverse side, we would like to use the graphic image of our logo only without the Sparrow Haulage name.

```html
<!DOCTYPE html>
<html lang="en">
<head>
<meta charset="utf-8">
<title>Sparrow Haulage – Business Card</title>
<link rel="stylesheet" href="https://fonts.googleapis.com/css2?family=Arimo:wght@400;700&display=swap">
<style>
  :root {
    --navy: #03045e;
    --red: #b40b0b;
    --white: #ffffff;
    --backdrop: #2b2b2b;
  }
  * { margin: 0; padding: 0; box-sizing: border-box; }
  html, body {
    width: 1200px;
    height: 1015px;
    overflow: hidden;
    background: var(--backdrop);
    font-family: "Arimo", Arial, sans-serif;
  }
  .sheet {
    width: 1200px;
    height: 1015px;
    display: flex;
    flex-direction: column;
    align-items: center;
    justify-content: center;
    gap: 45px;
  }
  .card {
    position: relative;
    width: 700px;
    height: 400px;
    background: var(--navy);
    overflow: hidden;
    box-shadow: 0 10px 30px rgba(0,0,0,0.5);
  }

  /* Back side */
  .card-back .brand-mark {
    position: absolute;
    top: 140px;
    left: 0;
    width: 100%;
    display: flex;
    align-items: center;
    justify-content: center;
    gap: 18px;
  }
  .card-back .brand-square {
    width: 34px;
    height: 34px;
    background: var(--red);
  }
  .card-back .brand-name {
    color: var(--white);
    font-weight: 700;
    font-size: 40px;
    letter-spacing: 3px;
  }
  .card-back .website {
    position: absolute;
    top: 300px;
    width: 100%;
    text-align: center;
    color: var(--white);
    font-size: 20px;
    letter-spacing: 1px;
  }
  .card-back .website .accent { color: var(--red); }

  /* Front side */
  .card-front .panel {
    position: absolute;
    inset: 0;
  }
  .card-front .holder {
    position: absolute;
    top: 48px;
    left: 44px;
  }
  .card-front .holder-name {
    color: var(--red);
    font-weight: 700;
    font-size: 30px;
    letter-spacing: 1px;
    text-transform: uppercase;
  }
  .card-front .holder-title {
    color: var(--white);
    font-size: 19px;
    margin-top: 2px;
    letter-spacing: 0.5px;
  }
  .card-front .contacts {
    position: absolute;
    left: 84px;
    top: 290px;
    list-style: none;
    color: var(--white);
    font-size: 18px;
    line-height: 24px;
  }
  .card-front .contacts .phone { font-weight: 700; }
  .card-front .brand-name {
    position: absolute;
    top: 150px;
    left: 455px;
    width: 235px;
    color: var(--navy);
    font-weight: 700;
    font-size: 30px;
    line-height: 34px;
    letter-spacing: 3px;
    text-transform: uppercase;
  }
</style>
</head>
<body>
<main class="sheet">

  <section class="card card-back" aria-label="Card back">
    <div class="brand-mark">
      <span class="brand-square"></span>
      <span class="brand-name">SPARROW HAULAGE</span>
    </div>
    <p class="website">WWW.<span class="accent">SPARROW-HAULAGE</span>.EXAMPLE</p>
  </section>

  <section class="card card-front" aria-label="Card front">
    <svg class="panel" width="700" height="400" viewBox="0 0 700 400" aria-hidden="true">
      <polygon points="405,0 700,0 700,400 605,400 405,287" fill="var(--white)"/>
      <polyline points="421,0 421,279 644,400" fill="none" stroke="var(--red)" stroke-width="7"/>
    </svg>

    <div class="holder">
      <h1 class="holder-name">Martin Obuya</h1>
      <p class="holder-title">CEO/FOUNDER</p>
    </div>

    <ul class="contacts">
      <li class="phone">555-206-7142</li>
      <li>www.sparrow-haulage.example</li>
      <li>martinobuya@sparrow-haulage.example</li>
    </ul>

    <p class="brand-name">Sparrow<br>Haulage</p>
  </section>

</main>
</body>
</html>
```